July 2022 Industrial Manufacturer Product Expo Mexico City

We manufacture large screws and fastners for large Mining equipment, Trains, large ships, airplanes, wind turbines, and so on. We also do custom work base on the customer needs. No matter the size we can make it.
We have a Expo coming up with companies all over the world. We have to stand out we are a family own business so our customer service will be above and beyond anyone can provide. We do not have a sales force to push our products and services we provide one on one service.
Plus@!! I'm looking for anything that you designers can come up with if it was your company to put on a business card, plus i want to do a 1 or 2 sided pamphlet, and then a website. We make Speciality Bolts for large mining equipment these bolts can be 3 to 4 foot long!!! Plus fasteners, Nuts, washers, any, size, strengths, special materials, we offer more of a ono on one customer service, We are a small company, family own, but can fulfill any type of orders. We can also provide special time lines for emergency orders. "We keep the machines running we here at KRV don't believe in down time" We want to hear any slogan based on our company to stand out.
Thanks i really appreciate all your work and options that we have to pick on. Plus just a thought we could possibly want to entertain a experience Marketing internet help maybe a employment possibility. Thanks

I need 2 cards one in Spanish and English Like the steel back ground maybe send me in some bright red and blue writing Same with the Black cards Please remove the word Military The logo KRV maybe integrate a picture of a Bolt 🔩 Thank you

Still looking for I need 2 cards one in Spanish and English Like the steel back ground maybe send me in some bright red and blue writing Same with the Black cards try bright writing Please remove the word Military The logo KRV maybe integrate a picture of a Bolt 🔩 Plus will need the company to make a brochure and website next Thank you

Target Market(s)

Large Mining, Ship, Train, Green Energy, VELM, and Government equipment. Throughout the World

Industry/Entity Type

We can Custom Manufacture any type of Fastners for Mining equipment, Trains, Ships, Green energy, Governments, or military projects. wind turbines,

Contact Information for Business Card

I attached the name and contact info that's on a card, plus the Company Logo. Would like industrial looking background with Bright Colors that will stand out!! If we can insert somewhere maybe on back that we "Custom Manufacture Any Size or Quantity Fastners for Large Mining Equipment, Trains, Ships, Green Energy Equipment or Government Projects

Font styles to use
Other font styles liked:
• You Pick, has to be bold, colorful standout, Professional looking Beable to read it.

Colors

Designer to choose colors to be used in the design.

Requirements
Must have
• Need in Spanish and English TO STANDOUT FROM THE REST OF THE EXPO!! See Business card details, Rounded corners
Nice to have
• Can i see some of the darker cards with Bright Red and Blue letters I like to see the different type of card material, heavy thickness, plastic, transparent, Metal types, Bright Colors, I saw like Raised letters like on the logo.

```html
<!DOCTYPE html>
<html lang="es">
<head>
<meta charset="utf-8">
<title>KRV Business Card</title>
<link rel="stylesheet" href="https://fonts.googleapis.com/css2?family=Tinos:wght@400;700&display=swap">
<style>
  :root {
    --stage: #2b2c2e;
    --card: #1b1c1e;
    --card-edge: #26272a;
    --ink-grey: #c4c6ca;
    --mark-grey: #a3a5aa;
    --bright-blue: #1fa8ff;
    --bright-red: #ff2a3a;
    --rule: #55575b;
    --white: #ffffff;
    --pattern-dark: #141517;
    --pattern-light: #3a3b3e;
  }
  * { box-sizing: border-box; margin: 0; padding: 0; }
  html, body {
    width: 1200px;
    height: 1108px;
    overflow: hidden;
    background: var(--stage);
    font-family: "Tinos", "Times New Roman", serif;
  }
  .stage {
    position: relative;
    width: 1200px;
    height: 1108px;
  }
  .card {
    position: absolute;
    top: 234px;
    width: 400px;
    height: 640px;
    border-radius: 24px;
    background: var(--card);
    border: 1px solid var(--card-edge);
    overflow: hidden;
    box-shadow: 0 18px 40px rgba(0,0,0,0.45);
  }
  .card--front { left: 170px; }
  .card--back { left: 630px; }

  .front-mark {
    position: absolute;
    top: 120px;
    left: 0;
    width: 100%;
    text-align: center;
    font-size: 104px;
    font-weight: 700;
    letter-spacing: 6px;
    color: var(--mark-grey);
    line-height: 1;
  }
  .front-details {
    position: absolute;
    top: 292px;
    left: 0;
    width: 100%;
    padding: 0 20px;
    text-align: center;
    color: var(--ink-grey);
  }
  .holder-name {
    font-size: 25px;
    color: var(--bright-blue);
    margin-bottom: 14px;
    white-space: nowrap;
  }
  .rule {
    width: 92px;
    height: 1px;
    background: var(--rule);
    margin: 10px auto;
  }
  .contact-line {
    font-size: 19px;
    line-height: 1.25;
  }
  .phone-label {
    color: var(--bright-red);
    font-weight: 700;
  }
  .services {
    font-size: 18px;
    line-height: 1.3;
    margin-top: 4px;
  }

  .back-pattern {
    position: absolute;
    inset: 0;
    background: linear-gradient(150deg, var(--pattern-dark) 0%, var(--pattern-light) 45%, var(--pattern-dark) 70%, #2e2f32 100%);
  }
  .back-mark {
    position: absolute;
    top: 392px;
    left: 0;
    width: 100%;
    text-align: center;
    font-size: 52px;
    font-weight: 700;
    letter-spacing: 3px;
    color: var(--white);
    line-height: 1;
  }
  .back-services {
    position: absolute;
    top: 470px;
    left: 0;
    width: 100%;
    padding: 0 28px;
    text-align: center;
    font-size: 17px;
    line-height: 1.3;
    color: var(--ink-grey);
  }
  .back-services .lead {
    color: var(--bright-red);
    font-weight: 700;
  }
</style>
</head>
<body>
<main class="stage">
  <section class="card card--front" aria-label="Card front, English">
    <div class="front-mark">KRV</div>
    <div class="front-details">
      <p class="holder-name">Lic. Mariana Soledad Ortega Ruiz</p>
      <div class="rule"></div>
      <p class="contact-line">Cotizaciones en</p>
      <p class="contact-line">ventas.krvtornillos@correo.mx</p>
      <div class="rule"></div>
      <p class="contact-line"><span class="phone-label">P:</span> 5550142318</p>
      <p class="contact-line"><span class="phone-label">M:</span> 5550179264</p>
      <div class="rule"></div>
      <p class="services">Custom Manufacture Any Size or Quantity<br>
      Fastners for Large Mining Equipment,<br>
      Trains, Ships, Green Energy Equipment<br>
      or Government Projects</p>
    </div>
  </section>

  <section class="card card--back" aria-label="Card back, Spanish" lang="es">
    <div class="back-pattern" role="img" aria-label="Repeating tone-on-tone company name pattern in glossy black"></div>
    <div class="back-mark">KRV</div>
    <p class="back-services"><span class="lead">Fabricación a la medida</span><br>
    Tornillería de cualquier tamaño o cantidad<br>
    para equipo minero, trenes, barcos,<br>
    energía verde o proyectos de gobierno</p>
  </section>
</main>
</body>
</html>
```